Responsive Mobile Quelvo Jewelry Template

We need to adapt an existing Quelvo template to be 100% responsive and mobile friendly. Due to Quelvo rules, the template would need to be implemented only using HTML and CSS (no Javascript). The template design files and HTML/CSS files are required for this project. We prefer that it is implemented using a responsive framework such as Gridwell.

An example of our current template can be found here (diamond only):
https://www.quelvo-market.example/itm/507318829106?ViewItem=&item=507318829106

And example of our template with an additional section for gemstone:
https://www.quelvo-market.example/itm/507318826673?ViewItem=&item=507318826673

We had also somewhat recently designed our Quelvo store landing page so some consistency with this would be desired:
http://www.quelvoshops.example/MirrowCraftNV

Please also refer to our website: https://mirrowcraftnv.example/

Target Market(s)

Primarily women shopping for jewelry on Quelvo.

Industry/Entity Type

Jewelry

Coding

Coded - Design and coding required

Number of Pages Required

1 page

Font styles to use
Sans Serif

Requirements
Must have
• * A color scheme that fits with the existing template design.
• * REMOVE the product photo in the template.
• * Sections required for Description, Basic Details, and Diamond/Gemstone Details.
• * Please refer to https://pages.quelvo-market.example/sell/itemdescription/mobilefriendlyguidelines.html in particular, the template must use
Nice to have
• * Menu of links to other categories is desired in a mobile friendly way.
• * We are open to graphics for links to popular categories similar to those found on the store page.
• * Implemented using a standardized responsive framework such as Gridwell.

```html
<!DOCTYPE html>
<html lang="en">
<head>
<meta charset="utf-8">
<title>Mirrow Craft – Item Template</title>
<link href="https://fonts.googleapis.com/css2?family=Lato:wght@400;700&family=Roboto:wght@400;500&display=swap" rel="stylesheet">
<style>
:root{
  --purple:#8366a0;
  --purple-dark:#6e4f8f;
  --lilac:#efe3fb;
  --lilac-deep:#d9c3f2;
  --tab-text:#8f6cad;
  --ink:#222;
  --body:#444;
  --rule:#d8d8d8;
  --white:#fff;
}
*{box-sizing:border-box;margin:0;padding:0}
html,body{width:972px;height:1200px;overflow:hidden;background:var(--white)}
body{font-family:"Roboto",sans-serif;color:var(--ink);position:relative}

.site-header{height:165px;background:linear-gradient(#e4d3fa 0%,#f6effd 70%,#fff 100%);border-bottom:1px solid #e2e2e2;position:relative}
.brand{position:absolute;left:0;right:0;top:20px;text-align:center;font-family:"Lato",sans-serif;color:var(--purple)}
.brand-mark{width:30px;height:30px;border-radius:50%;background:var(--lilac-deep);margin:0 auto 19px}
.brand-name{font-size:21px;letter-spacing:.5px;line-height:22px}
.brand-place{font-size:10px;letter-spacing:5.5px;margin-top:5px;color:#555}
.brand-rule{position:absolute;top:58px;height:6px;border-top:1px solid #b9a6cf;border-bottom:1px solid #b9a6cf}
.brand-rule.left{left:294px;width:87px}
.brand-rule.right{left:586px;width:92px}
.main-nav{position:absolute;top:126px;left:0;right:0;display:flex;justify-content:center;gap:31px;font-size:12.5px;font-weight:500;letter-spacing:.2px}
.main-nav .sep{font-weight:400}

.categories{position:absolute;left:90px;top:165px;width:792px;display:grid;grid-template-columns:repeat(5,1fr);border-left:1px solid var(--rule);border-bottom:1px solid var(--rule)}
.category{height:106px;border-right:1px solid var(--rule);text-align:center;padding-top:10px;font-size:12.8px;line-height:16px;color:#333}
.category:nth-child(-n+5){border-bottom:1px solid var(--rule)}
.category-icon{width:56px;height:54px;margin:0 auto 6px;border-radius:10px;background:linear-gradient(#e8dcf5,#d4c0ea)}

.panel{position:absolute;top:414px;width:381px;border:1px solid var(--rule)}
.panel.item{left:90px}
.panel.diamond{left:501px}
.panel-title{background:var(--purple);color:var(--white);font-family:"Lato",sans-serif;font-weight:700;font-size:16px;height:32px;line-height:33px;padding-left:22px;margin:-1px -1px 0}
.spec-row{display:grid;grid-template-columns:118px 58px 1fr;padding-left:23px;height:30px;align-items:center;font-size:11.4px;color:#444;border-top:1px solid var(--rule)}
.spec-row:first-of-type{border-top:none}
.spec-row.tall{height:33px}
.spec-row a{color:var(--purple-dark)}
.natural-note{position:absolute;left:90px;top:651px;font-size:13px;color:#444}

.tabs{position:absolute;left:90px;top:697px;width:792px;display:grid;grid-template-columns:repeat(5,1fr);gap:2px;background:var(--white)}
.tab{height:33px;line-height:33px;text-align:center;background:var(--lilac);color:var(--tab-text);font-size:13.5px}
.tab.active{background:var(--purple);color:var(--white)}
.tab-panel{position:absolute;left:90px;top:730px;width:792px;height:247px;border:1px solid var(--rule);border-top:none;padding:24px 28px 0 31px;font-size:11px;line-height:19px;color:#444}
.tab-panel h2{font-family:"Lato",sans-serif;font-weight:700;font-size:16.5px;color:var(--ink);margin:9px 0 17px}
.tab-panel p{margin-bottom:18px}
.tab-panel .shipping-rate{margin-bottom:0}

.trust-badges{position:absolute;top:1018px;left:0;right:0}
.badge{position:absolute;background:#d9d2e2}
.badge.rating{left:223px;top:2px;width:97px;height:70px;border-radius:4px}
.badge.lab{left:427px;top:0;width:120px;height:70px;border-radius:4px}
.badge.seal{left:663px;top:1px;width:70px;height:70px;border-radius:50%}

.newsletter{position:absolute;left:0;top:1126px;width:972px;height:74px;background:var(--purple)}
.newsletter h3{position:absolute;left:90px;top:22px;font-family:"Lato",sans-serif;font-weight:700;font-size:23px;color:var(--white)}
.signup{position:absolute;left:521px;top:20px;width:361px;height:34px;display:flex;border:1px solid var(--white)}
.signup .field{flex:1;padding-left:11px;line-height:32px;font-size:11.5px;color:var(--white)}
.signup .button{width:98px;background:var(--white);color:var(--purple);font-weight:500;font-size:13.5px;text-align:center;line-height:32px;letter-spacing:.3px}
</style>
</head>
<body>

<header class="site-header">
  <span class="brand-rule left"></span>
  <div class="brand">
    <div class="brand-mark"></div>
    <div class="brand-name">MIRROW CRAFT</div>
    <div class="brand-place">NEVADA</div>
  </div>
  <span class="brand-rule right"></span>
  <nav class="main-nav">
    <span>ABOUT US</span><span class="sep">|</span>
    <span>FAQS</span><span class="sep">|</span>
    <span>WHY BUY FROM US</span><span class="sep">|</span>
    <span>SAVE SELLER</span>
  </nav>
</header>

<section class="categories">
  <div class="category"><div class="category-icon" role="img" aria-label="Engagement rings icon"></div>Diamond Engagement<br>Rings</div>
  <div class="category"><div class="category-icon" role="img" aria-label="Fancy diamond icon"></div>Fancy Yellow &amp; Pink<br>Diamond</div>
  <div class="category"><div class="category-icon" role="img" aria-label="Cocktail rings icon"></div>Cocktail Fashion<br>Diamond Rings</div>
  <div class="category"><div class="category-icon" role="img" aria-label="Gemstone ring icon"></div>Colored Gemstone<br>Diamond Rings</div>
  <div class="category"><div class="category-icon" role="img" aria-label="Semi mount ring icon"></div>Semi Mount Diamond<br>Rings</div>
  <div class="category"><div class="category-icon" role="img" aria-label="Men's jewelry icon"></div>Men's Diamond<br>Jewelry</div>
  <div class="category"><div class="category-icon" role="img" aria-label="Pendant icon"></div>Diamond<br>Pendants</div>
  <div class="category"><div class="category-icon" role="img" aria-label="Earrings icon"></div>Diamond<br>Earrings</div>
  <div class="category"><div class="category-icon" role="img" aria-label="Necklace icon"></div>Diamond<br>Necklaces</div>
  <div class="category"><div class="category-icon" role="img" aria-label="Bracelet icon"></div>Diamond Bracelets<br>&amp; Bangles</div>
</section>

<section class="panel item">
  <h2 class="panel-title">ITEM DETAILS</h2>
  <div class="spec-row"><span>Model Number</span><span>:</span><span>MCN-RB52817KTE-600</span></div>
  <div class="spec-row"><span>Metal</span><span>:</span><span>14k Yellow Gold</span></div>
  <div class="spec-row"><span>Weight</span><span>:</span><span>4.08 grams</span></div>
  <div class="spec-row"><span>L x W x H</span><span>:</span><span>12 x 10 x 7.2 MM</span></div>
  <div class="spec-row"><span>Style</span><span>:</span><span>Halo</span></div>
  <div class="spec-row tall"><span>Ring Size</span><span>:</span><span>6 (contact us for sizing options)</span></div>
</section>
<p class="natural-note">All of our diamonds and gemstones are 100% natural!</p>

<section class="panel diamond">
  <h2 class="panel-title">DIAMOND DETAILS</h2>
  <div class="spec-row"><span>Total Carat Weight</span><span>:</span><span>0.19 CT</span></div>
  <div class="spec-row"><span>Diamond Count</span><span>:</span><span>22</span></div>
  <div class="spec-row"><span>Shape</span><span>:</span><span>Round</span></div>
  <div class="spec-row"><span>Color/Clarity:</span><span>:</span><span>G / SI1</span></div>
  <div class="spec-row"><span>Other Shape</span><span>:</span><span>Round</span></div>
  <div class="spec-row"><span>Other Color/Clarity</span><span>:</span><span>G / SI1</span></div>
  <div class="spec-row tall"><span>Certificate:</span><span>:</span><span>GRL (<a href="#">click for more info</a>)</span></div>
</section>

<nav class="tabs">
  <div class="tab active">Shipping Details</div>
  <div class="tab">Product Guarantee</div>
  <div class="tab">Return Policy</div>
  <div class="tab">Privacy Policy</div>
  <div class="tab">Why Mirrow Craft</div>
</nav>
<section class="tab-panel">
  <p class="shipping-rate">Parcelwing 2 Day: Free (U.S.A. only)</p>
  <h2>WE SHIP WORLDWIDE</h2>
  <p>International Buyers - Please Note: Import duties, taxes, &amp; charges are not included in the item price or shipping cost. These charges are the buyer's responsibility. Please check with your country's customs office to determine what these additional costs will be prior to bidding or buying.</p>
  <p>All packages are fully insured and require signature confirmation.</p>
  <p>Once your item(s) are ready to leave our facility a shipping tracking number will be sent to you. Business days do not include Saturday, Sunday or holidays. Please be sure to inspect your package upon arrival for tampering or any damage. Rush orders are welcome. Please call for availability.</p>
</section>

<div class="trust-badges">
  <div class="badge rating" role="img" aria-label="Business rating badge"></div>
  <div class="badge lab" role="img" aria-label="Gemological institute badge"></div>
  <div class="badge seal" role="img" aria-label="Gemological laboratory seal"></div>
</div>

<footer class="newsletter">
  <h3>ASK ANY QUESTIONS?</h3>
  <div class="signup">
    <span class="field">Enter Your Email</span>
    <span class="button">SUBSCRIBE</span>
  </div>
</footer>

</body>
</html>
```